Website design for Puddle Jump Kidscare

I need a website designed for my daycare business, Puddle Jump Kidscare, now that I have a new logo. My former website was ok but simple and I did not have a logo yet. It also was created by me using a template and was entirely pink. I loved the bright, happy feel of it but worried it might not appeal as much to potential clients who have sons. Therefore, I need a site which will appeal to both genders while still keeping the cheerful color scheme of my new logo, which has pinks, blue, green and cream.
Updates

Reason: Hello! I am still trying to download my new logo and am sorry it is taking me so long. Hopefully I will it posted by the end of today (US Eastern Standard Time). Thank you all very much for your patience!

Hello! I have finally managed to upload my new logo for you to use in designing my website. I'm sorry it took so long and greatly appreciate your time and creative efforts! I look forward to seeing what is submitted based on my logo design and its style/colors.

Many thanks!

Reason: As I've been traveling and posted my logo file late, I am extending my deadline. I am now back and can focus on providing more and better feedback. I appreciate your patience and submissions very much!

Reason: I need more time to provide feedback and make decisions.

Industry/Entity Type

Daycare

Colors
0192cd
33a6d7
86cae7
cadf82
fbf289
add136
e34197

```html
<!DOCTYPE html>
<html lang="en">
<head>
<meta charset="utf-8">
<title>Puddle Jump Kidscare</title>
<link href="https://fonts.googleapis.com/css2?family=Open+Sans:wght@400;600;700&display=swap" rel="stylesheet">
<style>
:root{
  --pink:#c4497c;
  --brown:#7b5c3e;
  --green:#7d9a18;
  --green-lt:#a9c932;
  --text:#555;
  --muted:#8a8a8a;
  --cream:#f7f4ec;
  --line:#ddd8cc;
  --dark:#2b2b2b;
  --icon:#3a3a3a;
}
*{margin:0;padding:0;box-sizing:border-box}
html,body{width:907px;height:1200px;overflow:hidden;background:#fff}
body{font-family:"Open Sans",Arial,sans-serif;color:var(--text);position:relative}
.site-header{position:absolute;left:0;top:0;width:907px;height:168px}
.brand{position:absolute;left:76px;top:52px;display:flex;align-items:center;gap:10px}
.brand-dot{width:34px;height:34px;border-radius:50%;background:var(--green-lt)}
.brand-name{font-size:27px;font-weight:600;color:var(--pink);line-height:30px;width:170px}
.social{position:absolute;right:76px;top:53px;display:flex;gap:3px}
.social span{width:22px;height:22px;border-radius:50%;background:var(--icon)}
.main-nav{position:absolute;right:76px;top:124px;font-size:12px;color:#444;letter-spacing:.2px}
.main-nav a{color:#444;text-decoration:none}
.main-nav a.active{color:var(--pink)}
.main-nav .sep{color:#aaa;margin:0 9px}
.hero{position:absolute;left:0;top:168px;width:907px;height:371px;
  background:linear-gradient(180deg,#e9edf3 0%,#dfe3ea 35%,#c9b8a8 70%,#8a7a6a 100%)}
.hero-arrow{position:absolute;top:185px;width:18px;height:18px}
.hero-caption{position:absolute;left:0;bottom:0;width:100%;height:48px;background:rgba(60,60,70,.55);
  color:#fff;font-weight:700;font-size:19.5px;text-align:center;line-height:48px;letter-spacing:.4px}
.features{position:absolute;left:77px;top:578px;display:flex;gap:0}
.feature{width:261px;display:flex;gap:6px}
.feature-icon{width:68px;height:68px;border-radius:50%;background:var(--brown);flex:none;display:flex;align-items:center;justify-content:center}
.feature h3{font-size:16.5px;font-weight:600;color:var(--brown);letter-spacing:.5px;margin-top:0;line-height:20px}
.feature p{font-size:9.2px;color:var(--muted);line-height:12.8px;width:160px;margin-top:2px}
.divider{position:absolute;left:75px;top:681px;width:757px;height:1px;background:#ddd}
.welcome{position:absolute;left:112px;top:710px;width:683px;text-align:center}
.welcome p{font-size:11.6px;line-height:17.5px;color:var(--text)}
.welcome .invite{font-size:15px;color:var(--green);margin-top:12px}
.news{position:absolute;left:0;top:846px;width:907px;height:125px;background:var(--cream);border-top:1px solid #ece6d6;border-bottom:1px solid #ece6d6}
.news h2{position:absolute;left:88px;top:17px;font-size:14.5px;font-weight:600;color:var(--brown)}
.news-arrows{position:absolute;left:803px;top:21px}
.news-rule{position:absolute;left:84px;top:42px;width:740px;height:1px;background:var(--line)}
.news-date{position:absolute;left:90px;top:59px;width:41px;height:45px;background:linear-gradient(180deg,var(--green-lt),#86a81c);color:#fff;text-align:center}
.news-date .day{display:block;font-size:17px;line-height:22px;margin-top:3px}
.news-date .mon{display:block;font-size:9.5px;line-height:12px}
.news-text{position:absolute;left:140px;top:57px;width:685px;font-size:10.2px;line-height:16px;color:#444}
.hours{position:absolute;left:0;top:995px;width:907px;text-align:center;font-size:22.5px;font-weight:600;color:var(--pink);letter-spacing:.5px}
.contact{position:absolute;left:0;top:1050px;width:907px;height:72px;background:var(--cream)}
.contact-item{position:absolute;display:flex;align-items:center;gap:10px;font-size:10.4px;color:#666;line-height:17px}
.site-footer{position:absolute;left:0;top:1122px;width:907px;height:78px;background:var(--dark);text-align:center;color:#ccc}
.footer-nav{margin-top:17px;font-size:10.2px}
.footer-nav a{color:#ccc;text-decoration:none}
.footer-nav .sep{margin:0 8px;color:#888}
.copyright{font-size:9.4px;margin-top:11px;color:#bbb}
</style>
</head>
<body>
<header class="site-header">
  <div class="brand"><span class="brand-dot"></span><span class="brand-name">Puddle Jump Kidscare</span></div>
  <div class="social" aria-label="Social links"><span></span><span></span><span></span><span></span></div>
  <nav class="main-nav">
    <a class="active" href="#">About us</a><span class="sep">/</span><a href="#">Services</a><span class="sep">/</span><a href="#">Hours and Fees</a><span class="sep">/</span><a href="#">Policies</a><span class="sep">/</span><a href="#">Contact us</a><span class="sep">/</span><a href="#">Gallery</a><span class="sep">/</span><a href="#">Testimonials</a>
  </nav>
</header>

<section class="hero" role="img" aria-label="Photo of four toddlers sitting together eating fruit in a bright playroom">
  <svg class="hero-arrow" style="left:77px" viewBox="0 0 18 18"><circle cx="9" cy="9" r="8" fill="none" stroke="#fff" stroke-width="1.5"/><path d="M10.5 5.5 7 9l3.5 3.5" fill="none" stroke="#fff" stroke-width="1.6"/></svg>
  <svg class="hero-arrow" style="left:812px" viewBox="0 0 18 18"><circle cx="9" cy="9" r="8" fill="none" stroke="#fff" stroke-width="1.5"/><path d="M7.5 5.5 11 9l-3.5 3.5" fill="none" stroke="#fff" stroke-width="1.6"/></svg>
  <div class="hero-caption">A PLAYSPACE WHERE CHILDREN CAN PLAY, CREATE, AND IMAGINE!</div>
</section>

<section class="features">
  <div class="feature">
    <div class="feature-icon"><svg width="36" height="30" viewBox="0 0 36 30"><path d="M3 4h12a3 3 0 0 1 3 3v20a3 3 0 0 0-3-3H3zM33 4H21a3 3 0 0 0-3 3v20a3 3 0 0 1 3-3h12z" fill="none" stroke="#fff" stroke-width="2.4"/></svg></div>
    <div><h3>LEARNING</h3><p>We develop age-appropriate activities that introduce and strengthen academic and social skills.</p></div>
  </div>
  <div class="feature">
    <div class="feature-icon"><svg width="34" height="34" viewBox="0 0 34 34" fill="none" stroke="#fff" stroke-width="2"><path d="M17 9a7 7 0 0 0-4 12.8V25h8v-3.2A7 7 0 0 0 17 9z"/><path d="M14 28h6M17 2v3M5 7l2 2M29 7l-2 2M2 17h3M29 17h3"/></svg></div>
    <div><h3>CREATIVITY</h3><p>We develop age-appropriate activities that introduce and strengthen academic and social skills.</p></div>
  </div>
  <div class="feature">
    <div class="feature-icon"><svg width="36" height="30" viewBox="0 0 36 30"><path d="M6 3h20v12a7 7 0 0 1-7 7h-6a7 7 0 0 1-7-7z" fill="#fff"/><path d="M26 6h3a4 4 0 0 1 0 8h-3" fill="none" stroke="#fff" stroke-width="2.4"/><rect x="2" y="25" width="30" height="3" fill="#fff"/></svg></div>
    <div><h3>SHARING</h3><p>We develop age-appropriate activities that introduce and strengthen academic and social skills.</p></div>
  </div>
</section>

<div class="divider"></div>

<section class="welcome">
  <p>Welcome to Puddle Jump Kidscare, a licensed Group Family Day Care, located in Maple Hill's beautiful Riverside district. We are located on a pretty, tree-lined block on Willowbrook Lane, between Oak and Cedar Streets. We are a few blocks from the Riverside train station and the Route 9 bus line, and we offer flexible hourly childcare, making it as easy as possible for busy parents on the go to arrange their children's care.</p>
  <p class="invite">We invite you to learn more about us and hope you will visit us soon!</p>
</section>

<section class="news">
  <h2>LATEST NEWS</h2>
  <svg class="news-arrows" width="20" height="10" viewBox="0 0 20 10"><path d="M7 1 1 5l6 4z" fill="#999"/><path d="M13 1l6 4-6 4z" fill="#777"/></svg>
  <div class="news-rule"></div>
  <div class="news-date"><span class="day">08</span><span class="mon">May</span></div>
  <p class="news-text">Nam a malesuada libero. Duis sodales et libero vel interdum. Interdum et malesuada fames ac ante ipsum primis in faucibus. Donec lobortis dui tortor, eu lobortis felis mattis nec. Sed justo quam, luctus eu mauris eget, euismod dapibus sem. Sed tempus feugiat ante, at ornare libero volutpat sed. Maecenas quis magna magna.</p>
</section>

<h2 class="hours">PLAYCARE HOURS ARE 8:00AM - 6:00PM</h2>

<section class="contact">
  <div class="contact-item" style="left:85px;top:18px">
    <svg width="18" height="20" viewBox="0 0 18 20"><rect x="1" y="1" width="16" height="18" fill="none" stroke="#888" stroke-width="2"/><path d="M6 1v10l3-2 3 2V1" fill="#888"/></svg>
    <span>52 Willowbrook Lane<br>Maple Hill, NY 10990</span>
  </div>
  <div class="contact-item" style="left:289px;top:26px">
    <svg width="22" height="22" viewBox="0 0 22 22"><path d="M3 2c-2 3 1 9 6 13s9 6 11 4l-3-4-3 2c-2-1-5-4-6-6l2-3z" fill="#888"/></svg>
    <span>Phone: (555) 014-2638</span>
  </div>
  <div class="contact-item" style="left:480px;top:26px">
    <svg width="22" height="22" viewBox="0 0 22 22"><rect x="2" y="8" width="18" height="13" fill="none" stroke="#888" stroke-width="2"/><rect x="6" y="2" width="10" height="7" fill="none" stroke="#888" stroke-width="1.6"/><path d="M6 12h2M10 12h2M14 12h2M6 16h2M10 16h2M14 16h2" stroke="#888" stroke-width="2"/></svg>
    <span>Fax : (555) 014-2639</span>
  </div>
  <div class="contact-item" style="left:667px;top:26px">
    <svg width="22" height="16" viewBox="0 0 22 16"><rect x="1" y="1" width="20" height="14" fill="#999"/><path d="M1 1l10 8 10-8" fill="none" stroke="#f7f4ec" stroke-width="1.5"/></svg>
    <span>E-mail : hello@puddlejumpkids.com</span>
  </div>
</section>

<footer class="site-footer">
  <nav class="footer-nav">
    <a href="#">Home</a><span class="sep">|</span><a href="#">About us</a><span class="sep">|</span><a href="#">Services</a><span class="sep">|</span><a href="#">Hours and Fees</a><span class="sep">|</span><a href="#">Policies</a><span class="sep">|</span><a href="#">Contact us</a><span class="sep">|</span><a href="#">Gallery</a><span class="sep">|</span><a href="#">Testimonials</a>
  </nav>
  <p class="copyright">Copyright &copy; 2014 &nbsp; Puddle Jump Kidscare. &nbsp; All rights reserved.</p>
</footer>
</body>
</html>
```